Business Card for my New Brokerage

Looking to get a business card design for my new Real Estate Brokerage.
I want it with Picture, Phone Number, Email, Website, Office Address
Name and Designation. Please add logo too.

Target Market(s)

Real Estate Investors or Home Buyers

Industry/Entity Type

Real Estate

Contact Information for Business Card

Name, Email, Phone Number, website, email, office address

Colors
EB3D1F
EC4F4E
F09395
F8D3D4
FCEDEE

Requirements
Must have
• Minimalistic, Clean, Modern, Photo
Nice to have
• White and Red Colors

```html
<!DOCTYPE html>
<html lang="en">
<head>
<meta charset="utf-8">
<title>Ember Realty Inc – Business Card</title>
<link rel="stylesheet" href="https://fonts.googleapis.com/css2?family=Montserrat:wght@500;700;800&family=Poppins:wght@400;500&display=swap">
<style>
  :root{
    --red:#dd1f26;
    --gold:#d9b54c;
    --gold-light:#f0d77e;
    --white:#ffffff;
    --ink:#2b2b2b;
    --bg:#e4e4e4;
    --suit:#2c4469;
    --shirt:#c9d8e8;
    --skin:#e9d2c2;
  }
  *{margin:0;padding:0;box-sizing:border-box}
  html,body{width:1200px;height:788px;overflow:hidden}
  body{background:var(--bg);position:relative;font-family:'Poppins',sans-serif}
  .card{position:absolute;width:540px;height:309px;border-radius:22px;overflow:hidden;box-shadow:0 10px 28px rgba(0,0,0,.22)}
  .card--front{left:40px;top:240px;background:var(--white)}
  .card--back{left:620px;top:240px;background:var(--red)}

  .front-bands{position:absolute;inset:0}
  .portrait{position:absolute;left:345px;top:34px;width:180px;height:275px;
    background:linear-gradient(180deg,var(--skin) 0%,var(--skin) 30%,var(--shirt) 36%,var(--suit) 58%,var(--suit) 100%);
    border-radius:70px 70px 0 0}

  .front-brand{position:absolute;left:30px;top:32px;color:var(--red);font-family:'Montserrat',sans-serif}
  .brand-name{font-weight:800;font-size:48px;line-height:1;letter-spacing:1px}
  .brand-sub{font-weight:500;font-size:13px;letter-spacing:6px;margin-top:4px;padding-left:60px}

  .front-name{position:absolute;left:30px;top:141px;color:var(--white)}
  .front-name .person{font-family:'Montserrat',sans-serif;font-weight:700;font-size:18px;letter-spacing:.5px}
  .front-name .role{font-size:11px;margin-top:-2px}

  .contact{position:absolute;left:30px;top:196px;color:var(--ink);font-size:11.5px;line-height:1.45}
  .contact li{list-style:none;display:flex;align-items:center;gap:7px}
  .contact .address{padding-left:19px}
  .contact svg{width:12px;height:12px;fill:var(--red);flex:none}

  .back-brand{position:absolute;left:0;right:0;top:96px;text-align:center;color:var(--white);font-family:'Montserrat',sans-serif}
  .back-brand .brand-name{font-size:86px}
  .back-brand .brand-sub{font-size:22px;letter-spacing:10px;margin-top:8px;padding-left:0}
</style>
</head>
<body>

<section class="card card--front" aria-label="Business card front">
  <svg class="front-bands" viewBox="0 0 540 309" aria-hidden="true">
    <defs>
      <linearGradient id="goldBand" x1="0" y1="1" x2="1" y2="0">
        <stop offset="0" stop-color="var(--gold)"/>
        <stop offset=".5" stop-color="var(--gold-light)"/>
        <stop offset="1" stop-color="var(--gold)"/>
      </linearGradient>
    </defs>
    <polygon points="300,184 540,40 540,96 372,184" fill="url(#goldBand)"/>
    <polygon points="0,130 352,130 306,184 0,184" fill="var(--red)"/>
  </svg>

  <div class="portrait" role="img" aria-label="Portrait photo of the broker in a navy blazer"></div>

  <div class="front-brand">
    <div class="brand-name">EMBER</div>
    <div class="brand-sub">REALTY INC</div>
  </div>

  <div class="front-name">
    <div class="person">DANIEL HART</div>
    <div class="role">Owner/CEO</div>
  </div>

  <ul class="contact">
    <li class="address">1450 W Maple Avenue</li>
    <li class="address">Cedar County Name 4180</li>
    <li><svg viewBox="0 0 24 24"><path d="M6.6 10.8a15.1 15.1 0 0 0 6.6 6.6l2.2-2.2c.3-.3.7-.4 1-.2 1.1.4 2.3.6 3.6.6.6 0 1 .4 1 1V20c0 .6-.4 1-1 1A17 17 0 0 1 3 4c0-.6.4-1 1-1h3.5c.6 0 1 .4 1 1 0 1.3.2 2.5.6 3.6.1.3 0 .7-.2 1z"/></svg>555-214-78360</li>
    <li><svg viewBox="0 0 24 24"><path d="M2 5h20v14H2zm2 2v.5l8 5 8-5V7zm0 2.8V17h16V9.8l-8 5z"/></svg>info@emberrealtyinc.com</li>
    <li><svg viewBox="0 0 24 24"><path d="M12 2a10 10 0 1 0 0 20 10 10 0 0 0 0-20zm0 2c.8 1.2 1.5 2.5 1.9 4h-3.8c.4-1.5 1.1-2.8 1.9-4zM4.3 14a8 8 0 0 1 0-4h3.4a16 16 0 0 0 0 4zm.8 2h3a15 15 0 0 0 1.3 3.9A8 8 0 0 1 5.1 16zm3-8h-3a8 8 0 0 1 4.3-3.9C8.8 5.3 8.4 6.6 8.1 8zM12 20c-.8-1.2-1.5-2.5-1.9-4h3.8c-.4 1.5-1.1 2.8-1.9 4zm2.3-6H9.7a14 14 0 0 1 0-4h4.6a14 14 0 0 1 0 4zm.3 5.9c.6-1.2 1-2.5 1.3-3.9h3a8 8 0 0 1-4.3 3.9zm1.7-5.9a16 16 0 0 0 0-4h3.4a8 8 0 0 1 0 4zm-.4-6a15 15 0 0 0-1.3-3.9A8 8 0 0 1 18.9 8z"/></svg>www.emberrealtyinc.com</li>
  </ul>
</section>

<section class="card card--back" aria-label="Business card back">
  <div class="back-brand">
    <div class="brand-name">EMBER</div>
    <div class="brand-sub">REALTY INC</div>
  </div>
</section>

</body>
</html>
```